Book cover

I am working with my publisher to publish my book They came up with a book cover but I don't like it. I want to see different designs. The book Title is Brightwater the subtitle Ways to Guide Teams Through Storms with Poise, Purpose & Pace by Marlene T. Ostrowski
I want to use my Brand Colors including the blue. I am uploading the covers of my other book. This is a professional leadership book. The publisher will make the cover when providing them a new design. the Brightwater one is one I played with on Canva. I would like more color and to incorporate the blue. I want a spot at the top where I can write a quote. Brightwater is one word in the text so should be the same on the cover. I want the cover to show energy movement and am open to an image too. I am attaching logos for the feel of the brand and brand rgb codes.

```html
<!DOCTYPE html>
<html lang="en">
<head>
<meta charset="utf-8">
<title>Brightwater — Book Cover</title>
<link href="https://fonts.googleapis.com/css2?family=Montserrat:wght@300;400;600;800&family=Arvo:wght@700&display=swap" rel="stylesheet">
<style>
  :root {
    --paper: #f3f3f1;
    --mist-teal: rgba(120, 215, 225, 0.22);
    --mist-amber: rgba(245, 190, 120, 0.22);
    --teal: #1aa3b3;
    --coral: #e8705c;
    --band: #e96b56;
    --title-grey: #5e5a5d;
    --art-red: #d8321f;
    --art-charcoal: #3f3f42;
    --white: #ffffff;
  }
  * { margin: 0; padding: 0; box-sizing: border-box; }
  html, body { width: 980px; height: 1200px; overflow: hidden; background: var(--paper); }
  .cover {
    position: relative;
    width: 980px;
    height: 1200px;
    overflow: hidden;
    background:
      radial-gradient(ellipse 260px 180px at 160px 280px, var(--mist-amber), transparent 70%),
      radial-gradient(ellipse 300px 220px at 480px 420px, var(--mist-teal), transparent 70%),
      radial-gradient(ellipse 260px 200px at 860px 600px, var(--mist-teal), transparent 70%),
      var(--paper);
    font-family: "Montserrat", sans-serif;
  }
  .quote-line {
    position: absolute;
    left: 232px;
    top: 158px;
    width: 620px;
    color: var(--teal);
    font-weight: 600;
    font-size: 19.5px;
    line-height: 26px;
    letter-spacing: 0.2px;
    text-transform: uppercase;
  }
  .title-artwork {
    position: absolute;
    left: 57px;
    top: 415px;
    width: 215px;
    height: 358px;
    background: linear-gradient(180deg, var(--art-red) 0%, #b92a1c 45%, var(--art-charcoal) 55%, #5a5a5d 100%);
  }
  .book-title {
    position: absolute;
    left: 288px;
    top: 708px;
    font-weight: 800;
    font-size: 72px;
    line-height: 72px;
    letter-spacing: -1px;
    white-space: nowrap;
    text-transform: uppercase;
  }
  .title-bright { color: var(--title-grey); }
  .title-water { color: var(--coral); }
  .subtitle-band {
    position: absolute;
    left: 0;
    top: 868px;
    width: 980px;
    height: 130px;
    background: var(--band);
    color: var(--white);
    text-align: center;
    padding-top: 33px;
  }
  .subtitle-lead { font-weight: 300; font-size: 28px; line-height: 34px; letter-spacing: 0.5px; }
  .subtitle-values { font-weight: 400; font-size: 26px; line-height: 32px; letter-spacing: 0.8px; text-transform: uppercase; }
  .author {
    position: absolute;
    left: 0;
    top: 1078px;
    width: 980px;
    text-align: center;
    font-family: "Arvo", serif;
    font-weight: 700;
    font-size: 42px;
    line-height: 48px;
    color: var(--teal);
    text-transform: uppercase;
  }
</style>
</head>
<body>
<main class="cover">
  <p class="quote-line">Brightwater is the essential playbook<br>to turn your uncertainty into possibility</p>

  <div class="title-artwork" role="img" aria-label="Abstract textured artwork in red and charcoal tones beside the title"></div>

  <h1 class="book-title"><span class="title-bright">Bright</span><span class="title-water">water</span></h1>

  <section class="subtitle-band">
    <p class="subtitle-lead">Ways to Guide Teams Through Storms with</p>
    <p class="subtitle-values">Poise, Purpose &amp; Pace</p>
  </section>

  <p class="author">Marlene T. Ostrowski</p>
</main>
</body>
</html>
```